Need a clean & modern homepage for an education site + opportunity for longer term work

Thanks for viewing our project. We are excited about this new website and we hope that we might build a relationship with designers as we work on this project. I provided quite a few details and requirements to help you more quickly create a design that meets our needs.
Who we are:
We are a website that discusses the importance of college accreditation and provides a directory of college programs.
What we need:
A homepage that meets the below requirements and is inspired by the examples provided
Definition of accredited:
ac·cred·it·ed [uh-kred-i-tid] adj.
1. officially recognized as meeting the essential requirements, as of academic excellence: accredited schools.
2. provided with official credentials, as by a government: an accredited diplomatic representative.
3. accepted as authoritative: an accredited theory.
Overall look and feel for the homepage:
- Clean, simple and modern
- Limited (or zero) pictures
- Utilize color blocks with text
- A trend seems to be longer vertical length homepages with lots of whitespace. I generally like this trend as long as the page is not way to tall.
Inspirations: Sites that have a similar look and feel to what I need.
http://lernvoxa.org/
http://www.campusmetrik.com/colleges/brantmoor-university/
http://quietfolding.org/
http://www.velostrahiring.com/
http://www.zunq.com/
http://sketches.bxv.com/
Items to be included on the homepage. Details below on each item.
- Top navigation
- Logo: Please leave a blank area for a logo. The logo has not been designed.
- Simple graphic/color block at the top that highlights a definition of “Accredited” – the definition should be formatted like it is being copy/pasted from a dictionary.
- Space for a video and small (50 word) written description of the video. You can use placeholder text.
- One section with 3 Paragraphs of content (each paragraph around 100 words) with a header at the top. You can use placeholder text but please create the formatting. At the end of the 3 paragraphs please have a “Read More” Note this shouldn't be 3 separate paragraphs with three read mores - it is 3 paragraphs with one read more at the end.
- An area with the header “Search Colleges by State” that has anchor text links to all 50 states.
Top navigation:
- Home
- States – with a subnav dropdown that includes all 50 US states.
- Programs – with a subnav dropdown that includes program titles (list below)
- Degrees - with a subnav dropdown that includes 5 degree levels (list below)
- Accreditation – no subnav
- Rankings – no subnav
- Resources – no subnav
Footer
- Link to about us, privacy, and a copyright www.url.com
Programs List for sub navigation
Accounting
Art
Bible
Business
Criminal Justice
Design
Education
Engineering
English
Law
LPN to RN
Management
Math
MBA
MPH
Medical Assisting
Military
Nursing
Occupational Therapy
Paralegal
Psychology
Pharmacy
RN to BSN
Radiology
Social Work
Sonography
Degrees list for sub navigation
Certificate
Associate
Bachelors
Masters
PhD
Thanks so much - looking forward to working with you!
Education

```html
<!DOCTYPE html>
<html lang="en">
<head>
<meta charset="utf-8">
<title>Accredora — Accredited College Directory</title>
<link rel="stylesheet" href="https://fonts.googleapis.com/css2?family=Montserrat:wght@400;500;600;700&family=Mulish:ital,wght@0,400;0,600;1,400&display=swap">
<style>
  :root {
    --coral: #e05f52;
    --coral-dark: #c94a3e;
    --charcoal: #444444;
    --ink: #333333;
    --muted: #8a8a8a;
    --sky: #bed3df;
    --sky-line: #d5e3eb;
    --map: #cbdce6;
    --paper: #f7f7f7;
    --white: #ffffff;
    --pron: #a9cde0;
    --progress: #29b6c4;
  }
  * { box-sizing: border-box; margin: 0; padding: 0; }
  html, body { width: 1200px; height: 2584px; overflow: hidden; }
  body {
    position: relative;
    background: var(--paper);
    font-family: "Mulish", sans-serif;
    color: var(--ink);
  }
  .abs { position: absolute; }

  /* Header */
  .site-header { left: 0; top: 0; width: 1200px; height: 147px; background: var(--paper); }
  .logo-slot {
    left: 140px; top: 36px;
    font-family: "Montserrat", sans-serif; font-weight: 700;
    font-size: 35px; line-height: 39px; color: var(--coral); letter-spacing: 0;
  }
  .social { right: 138px; top: 40px; display: flex; gap: 8px; }
  .social span {
    width: 28px; height: 28px; background: var(--charcoal); color: var(--white);
    font-family: "Montserrat", sans-serif; font-size: 13px; font-weight: 600;
    display: flex; align-items: center; justify-content: center;
  }
  .main-nav { left: 324px; top: 93px; width: 740px; display: flex; justify-content: space-between; }
  .main-nav a {
    font-family: "Montserrat", sans-serif; font-size: 15px; font-weight: 500;
    color: var(--ink); text-decoration: none; letter-spacing: .2px; white-space: nowrap;
  }
  .main-nav a.has-sub::after { content: " ▾"; font-size: 9px; vertical-align: 2px; }

  /* Definition band */
  .definition-band { left: 0; top: 147px; }
  .definition-term { left: 169px; top: 186px; color: var(--white); }
  .definition-term .label { font-size: 25px; letter-spacing: 1px; font-family: "Montserrat", sans-serif; }
  .definition-term .word { font-family: "Montserrat", sans-serif; font-size: 38px; font-weight: 600; margin-top: 6px; }
  .definition-term .pron { font-style: italic; font-size: 30px; color: var(--pron); margin-top: -2px; }
  .definition-term .pos { font-style: italic; font-size: 20px; color: var(--muted); margin-top: 6px; }
  .definition-list { left: 469px; top: 184px; width: 510px; list-style: none; color: var(--white); font-size: 15px; line-height: 22px; }
  .definition-list li { margin-bottom: 22px; }

  /* Topics */
  .topics-band { left: 0; top: 379px; }
  .topic { width: 300px; text-align: center; }
  .topic h2 { font-family: "Montserrat", sans-serif; font-size: 30px; font-weight: 600; color: var(--ink); margin-bottom: 18px; }
  .topic p { width: 264px; margin: 0 auto; font-size: 14.5px; line-height: 22px; color: #4d5358; }

  /* Video */
  .video-copy { left: 140px; top: 892px; width: 320px; font-size: 15px; line-height: 28px; color: var(--ink); }
  .video-player { left: 545px; top: 848px; width: 517px; height: 345px; background: var(--charcoal); border-radius: 6px; overflow: hidden; }
  .video-screen { position: absolute; left: 8px; top: 8px; width: 501px; height: 282px; background: linear-gradient(135deg, #6b5446, #4e4038 55%, #75614f); }
  .play-btn { position: absolute; left: 234px; top: 124px; width: 36px; height: 36px; background: var(--white); border-radius: 3px; }
  .play-btn::after { content: ""; position: absolute; left: 13px; top: 10px; border-left: 13px solid var(--ink); border-top: 8px solid transparent; border-bottom: 8px solid transparent; }
  .progress { position: absolute; left: 14px; top: 316px; width: 420px; height: 9px; background: #cfcfcf; border-radius: 2px; }
  .progress .done { width: 125px; height: 9px; background: var(--progress); }
  .progress .knob { position: absolute; left: 120px; top: -4px; width: 10px; height: 17px; background: var(--white); border-radius: 2px; }

  /* Paragraphs */
  .paragraphs-title { left: 0; top: 1342px; width: 1200px; text-align: center; font-family: "Montserrat", sans-serif; font-size: 30px; font-weight: 700; color: var(--white); letter-spacing: .5px; }
  .paragraph { top: 1422px; width: 278px; text-align: center; font-size: 14.5px; line-height: 22px; color: var(--white); }
  .read-more-shadow { left: 497px; top: 1652px; width: 206px; height: 42px; background: var(--coral-dark); }
  .read-more { left: 515px; top: 1634px; width: 171px; height: 46px; background: var(--white); color: var(--coral); font-family: "Montserrat", sans-serif; font-weight: 700; font-size: 15px; letter-spacing: 2px; display: flex; align-items: center; justify-content: center; text-decoration: none; }

  /* States */
  .state-map { left: 110px; top: 1780px; width: 980px; height: 630px; background: var(--map); border-radius: 120px 260px 200px 220px / 90px 160px 260px 200px; }
  .states-title { left: 0; top: 1782px; width: 1200px; text-align: center; font-family: "Montserrat", sans-serif; font-size: 39px; font-weight: 600; color: var(--charcoal); letter-spacing: 3px; }
  .state-column { top: 1906px; list-style: none; }
  .state-column li { font-size: 15px; line-height: 33.3px; color: #4a4f54; }
  .state-column a { color: inherit; text-decoration: none; }

  /* Footer */
  .footer-band { left: 0; top: 2430px; }
  .copyright { left: 0; top: 2497px; width: 1200px; text-align: center; font-family: "Montserrat", sans-serif; font-size: 12.5px; color: var(--white); letter-spacing: .5px; }
  .footer-links { left: 0; top: 2532px; width: 1200px; text-align: center; font-family: "Montserrat", sans-serif; font-size: 11.5px; }
  .footer-links a { color: var(--white); text-decoration: none; padding: 0 8px; }
  .footer-links a + a { border-left: 1px solid #888; }
</style>
</head>
<body>

<header class="site-header abs">
  <div class="logo-slot abs">LOGO<br>HERE</div>
  <div class="social abs">
    <span aria-label="Kinnect">K</span>
    <span aria-label="Vocle">V</span>
    <span aria-label="Qorum">Q</span>
  </div>
  <nav class="main-nav abs">
    <a href="#">HOME</a>
    <a href="#" class="has-sub">STATES</a>
    <a href="#" class="has-sub">PROGRAMS</a>
    <a href="#" class="has-sub">DEGREES</a>
    <a href="#">ACCREDITATION</a>
    <a href="#">RANKINGS</a>
    <a href="#">RESOURCES</a>
  </nav>
</header>

<svg class="definition-band abs" width="1200" height="640" viewBox="0 0 1200 640">
  <polygon points="0,0 1200,0 1200,232 600,279 0,232" fill="#444444"/>
</svg>
<svg class="topics-band abs" width="1200" height="410" viewBox="0 0 1200 410">
  <polygon points="0,0 600,47 1200,0 1200,388 0,388" fill="#bed3df"/>
  <line x1="383" y1="30" x2="479" y2="388" stroke="#d5e3eb" stroke-width="3"/>
  <line x1="818" y1="30" x2="724" y2="388" stroke="#d5e3eb" stroke-width="3"/>
  <rect x="0" y="388" width="1200" height="6" fill="#ffffff"/>
  <rect x="0" y="394" width="1200" height="8" fill="#bed3df"/>
</svg>

<div class="definition-term abs">
  <div class="label">“ACCREDITED”</div>
  <div class="word">ac·cred·it·ed</div>
  <div class="pron">[uh-kred-i-tid]</div>
  <div class="pos">adjective</div>
</div>
<ol class="definition-list abs">
  <li>1. officially recognized as meeting the essential requirements, as of academic excellence: accredited schools.</li>
  <li>2. provided with official credentials, as by a government: an accredited diplomatic representative.</li>
  <li>3. accepted as authoritative: an accredited theory.</li>
</ol>

<section class="topic abs" style="left:117px; top:504px;">
  <h2>Rankings</h2>
  <p>Egestas amet nullam dis. Ullamcorper netus cum accumsan pellentesque cubilia diam. A luctus turpis Rutrum fames quam integer. Etiam porta diam suspendisse habitant lacinia pede ad tristique</p>
</section>
<section class="topic abs" style="left:450px; top:477px;">
  <h2>Accreditation</h2>
  <p>Massa commodo hendrerit blandit cras habitasse suspendisse eros pellentesque vel facilisis sodales, nulla volutpat conubia aliquet aptent eleifend commodo vitae hendrerit sociis potenti et bibendum mus</p>
</section>
<section class="topic abs" style="left:783px; top:504px;">
  <h2>Resources</h2>
  <p>Iaculis fermentum pellentesque sociosqu amet aenean netus, donec laoreet luctus. Accumsan nullam habitant felis Erat morbi taciti elit cubilia dapibus enim euismod ultricies penatibus velit</p>
</section>

<p class="video-copy abs">Quam praesent. Ullamcorper dolor primis natoque dolor. Erat mollis. Aliquam facilisis. Vestibulum pharetra natoque pulvinar nec. Praesent risus, morbi lobortis odio pretium aptent. Hendrerit ligula varius iaculis nonummy enim. Pulvinar mauris quam eleifend, iaculis vestibulum cras, dui nullam vulputate eu Ridiculus sit platea quis mi. Cubilia netus purus nunc etiam.</p>

<div class="video-player abs">
  <div class="video-screen" role="img" aria-label="Video still of a desk with notebooks, keyboard and stationery"></div>
  <div class="play-btn"></div>
  <div class="progress"><div class="done"></div><div class="knob"></div></div>
  <svg style="position:absolute; left:454px; top:312px;" width="50" height="18" viewBox="0 0 50 18">
    <polygon points="1,6 5,6 10,2 10,16 5,12 1,12" fill="#ffffff"/>
    <path d="M13,5 Q16,9 13,13" stroke="#ffffff" stroke-width="1.6" fill="none"/>
    <path d="M32,1 h5 M32,1 v5 M49,1 h-5 M49,1 v5 M32,17 h5 M32,17 v-5 M49,17 h-5 M49,17 v-5" stroke="#ffffff" stroke-width="2" fill="none"/>
  </svg>
</div>

<svg class="abs" style="left:0; top:1195px;" width="1200" height="610" viewBox="0 0 1200 610">
  <rect x="0" y="40" width="1200" height="500" fill="#e05f52"/>
  <ellipse cx="600" cy="52" rx="640" ry="46" fill="#ffffff"/>
  <rect x="0" y="0" width="1200" height="46" fill="#f7f7f7"/>
  <ellipse cx="600" cy="52" rx="630" ry="44" fill="#ffffff"/>
  <ellipse cx="600" cy="535" rx="640" ry="65" fill="#ffffff"/>
  <rect x="0" y="540" width="1200" height="70" fill="#f7f7f7"/>
</svg>

<h2 class="paragraphs-title abs">PARAGRAPHS TITLE</h2>
<p class="paragraph abs" style="left:140px;">Facilisi curae justo facilisis porta pede vivamus sem urna eget. Condimentum ad vel feugiat ad aliquam ornare taciti Lorem Suspendisse Congue quisque nostra lacinia, pharetra lacinia rhoncus venenatis nullam id montes suspendisse vehicula blandit tortor pellentesque sociis.</p>
<p class="paragraph abs" style="left:461px;">Nullam rutrum parturient viverra netus dictum felis purus lacinia amet Senectus ante Penatibus augue molestie eros pretium mauris. Faucibus condimentum convallis. Blandit porta lorem ante et gravida litora mus.</p>
<p class="paragraph abs" style="left:783px;">Velit litora, interdum augue, dapibus vel ornare condimentum quis dis dolor rutrum malesuada. Dapibus aptent orci mi non nibh quisque donec. Vestibulum litora arcu varius mus dapibus nascetur. Nonummy hendrerit sociis ullamcorper interdum.</p>
<div class="read-more-shadow abs"></div>
<a class="read-more abs" href="#">READ MORE</a>

<div class="state-map abs" role="img" aria-label="Map of the United States divided into states"></div>
<h2 class="states-title abs">SEARCH COLLEGES BY STATE</h2>
<ul class="state-column abs" style="left:167px;">
  <li><a href="#">Alabama</a></li><li><a href="#">Alaska</a></li><li><a href="#">Arizona</a></li><li><a href="#">Arkansas</a></li><li><a href="#">California</a></li><li><a href="#">Colorado</a></li><li><a href="#">Connecticut</a></li><li><a href="#">Delaware</a></li><li><a href="#">Florida</a></li><li><a href="#">Georgia</a></li>
</ul>
<ul class="state-column abs" style="left:360px;">
  <li><a href="#">Hawaii</a></li><li><a href="#">Idaho</a></li><li><a href="#">Illinois</a></li><li><a href="#">Indiana</a></li><li><a href="#">Iowa</a></li><li><a href="#">Kansas</a></li><li><a href="#">Kentucky</a></li><li><a href="#">Louisiana</a></li><li><a href="#">Maine</a></li><li><a href="#">Maryland</a></li>
</ul>
<ul class="state-column abs" style="left:536px;">
  <li><a href="#">Massachusetts</a></li><li><a href="#">Michigan</a></li><li><a href="#">Minnesota</a></li><li><a href="#">Mississippi</a></li><li><a href="#">Missouri</a></li><li><a href="#">Montana</a></li><li><a href="#">Nebraska</a></li><li><a href="#">Nevada</a></li><li><a href="#">New Hampshire</a></li><li><a href="#">New Jersey</a></li>
</ul>
<ul class="state-column abs" style="left:738px;">
  <li><a href="#">New Mexico</a></li><li><a href="#">New York</a></li><li><a href="#">North Carolina</a></li><li><a href="#">North Dakota</a></li><li><a href="#">Ohio</a></li><li><a href="#">Oklahoma</a></li><li><a href="#">Oregon</a></li><li><a href="#">Pennsylvania</a></li><li><a href="#">Rhode Island</a></li><li><a href="#">South Carolina</a></li>
</ul>
<ul class="state-column abs" style="left:933px;">
  <li><a href="#">South Dakota</a></li><li><a href="#">Tennessee</a></li><li><a href="#">Texas</a></li><li><a href="#">Utah</a></li><li><a href="#">Vermont</a></li><li><a href="#">Virginia</a></li><li><a href="#">Washington</a></li><li><a href="#">West Virginia</a></li><li><a href="#">Wisconsin</a></li><li><a href="#">Wyoming</a></li>
</ul>

<svg class="footer-band abs" width="1200" height="154" viewBox="0 0 1200 154">
  <polygon points="0,53 600,3 1200,53 1200,154 0,154" fill="#444444"/>
</svg>
<p class="copyright abs">COPYRIGHT © 2013 WWW.ACCREDORA.COM. ALL RIGHTS RESERVED.</p>
<nav class="footer-links abs"><a href="#">ABOUT US</a><a href="#">PRIVACY</a></nav>

</body>
</html>
```